New Webpage for High Class Expert Witness Services Company

We are looking for a minimalist design for a webpage that just has our logo and an entry form offer to connect with one of our Liaisons.
The entry form should just ask for Name, Email, Contact Info and Description of Project.

Company Name is: The Marlowe Crest Advisory Services

Number of Pages Required

1 page

```html
<!DOCTYPE html>
<html lang="en">
<head>
<meta charset="UTF-8">
<title>The Marlowe Crest Advisory Services — Initiate Consultation</title>
<link href="https://fonts.googleapis.com/css2?family=Cinzel:wght@700&family=Inter:wght@400;500&display=swap" rel="stylesheet">
<style>
  :root {
    --page-bg: #f6f6f7;
    --page-tone: #e9e9ec;
    --ink-dark: #4a4a4c;
    --ink-mid: #5e5e61;
    --ink-soft: #666669;
    --card-bg: #e1e2e5;
    --card-tone: #d3d4d8;
    --field-bg: #ffffff;
    --button-top: #f2f2f3;
    --button-bottom: #9c9ca0;
    --button-ink: #111113;
  }
  * { box-sizing: border-box; margin: 0; padding: 0; }
  html, body { width: 1200px; height: 813px; overflow: hidden; }
  body {
    position: relative;
    font-family: "Inter", sans-serif;
    color: var(--ink-mid);
    background: var(--page-bg);
  }
  .page-texture {
    position: absolute; inset: 0;
    background: radial-gradient(ellipse at 50% 45%, var(--page-bg) 30%, var(--page-tone) 100%);
  }
  .brand {
    position: absolute; left: 0; right: 0; top: 88px;
    text-align: center;
  }
  .brand-name {
    font-family: "Cinzel", serif; font-weight: 700;
    font-size: 42px; line-height: 48px; letter-spacing: 1px;
    color: var(--ink-dark);
  }
  .consult-card {
    position: absolute; left: 111px; top: 220px;
    width: 978px; height: 521px;
    border-radius: 43px; overflow: hidden;
    background: var(--card-bg);
  }
  .card-photo {
    position: absolute; inset: 0;
    background: linear-gradient(110deg, var(--card-bg) 0%, var(--card-tone) 35%, var(--card-bg) 60%, #dcdde0 100%);
    opacity: .8;
  }
  .intro {
    position: absolute; left: 48px; top: 50px; width: 440px;
  }
  .intro-kicker {
    font-family: "Cinzel", serif; font-weight: 700;
    font-size: 23px; line-height: 28px; letter-spacing: .5px; color: var(--ink-soft);
  }
  .intro-title {
    margin-top: 2px;
    font-family: "Cinzel", serif; font-weight: 700;
    font-size: 40px; line-height: 48px; color: var(--ink-soft);
  }
  .intro-text {
    margin-top: 18px; width: 392px;
    font-size: 16px; line-height: 32px; color: var(--ink-soft);
  }
  .liaison-form { position: absolute; left: 523px; top: 52px; width: 406px; }
  .field {
    position: relative; display: block;
    height: 51px; margin-bottom: 21px;
    background: var(--field-bg); border-radius: 12px;
  }
  .field span {
    position: absolute; left: 26px; top: 17px;
    font-size: 14.5px; color: var(--ink-mid);
  }
  .field svg { position: absolute; right: 26px; top: 17px; width: 16px; height: 16px; fill: #3c3c3e; }
  .field-overview { height: 128px; }
  .submit-btn {
    position: absolute; left: 213px; top: 374px;
    width: 193px; height: 43px;
    border: 1px solid #bdbdc0; border-radius: 9px;
    background: linear-gradient(90deg, var(--button-top), var(--button-bottom));
    box-shadow: 0 8px 24px rgba(0,0,0,.12);
    font-family: "Inter", sans-serif; font-size: 15.5px; color: var(--button-ink);
  }
  .site-footer {
    position: absolute; left: 0; right: 0; top: 770px;
    text-align: center; font-size: 15px; color: var(--ink-mid);
  }
</style>
</head>
<body>
  <div class="page-texture" role="img" aria-label="Soft grey halftone dot wave background"></div>

  <header class="brand">
    <div class="brand-name">The Marlowe Crest Advisory Services</div>
  </header>

  <main class="consult-card">
    <div class="card-photo" role="img" aria-label="Faded photograph of a physician holding a stethoscope"></div>

    <section class="intro">
      <p class="intro-kicker">PRECISION. CREDIBILITY.</p>
      <h1 class="intro-title">DEFENSE WITHOUT COMPROMISE.</h1>
      <p class="intro-text">Connect with a dedicated liaison to engage highly qualified expert witnesses for complex, high-stakes matters.</p>
    </section>

    <form class="liaison-form">
      <label class="field"><span>Full Name</span>
        <svg viewBox="0 0 16 16"><circle cx="8" cy="4.5" r="3.3"/><path d="M1.5 15c0-4 3-6 6.5-6s6.5 2 6.5 6z"/></svg>
      </label>
      <label class="field"><span>Email Address</span>
        <svg viewBox="0 0 16 16"><path d="M1 3h14v10H1z M2.5 4.5v.3L8 9l5.5-4.2v-.3z" fill-rule="evenodd"/></svg>
      </label>
      <label class="field"><span>Contact Number</span>
        <svg viewBox="0 0 16 16"><path d="M1 6c1-3 13-3 14 0l-.5 1.5-3-.5V5.5C10 5 6 5 4.5 5.5V7l-3 .5z"/><path d="M4 8h8l2 6H2z M8 9.3a2 2 0 1 0 0 4 2 2 0 0 0 0-4z" fill-rule="evenodd"/></svg>
      </label>
      <label class="field field-overview"><span>Project Overview</span>
        <svg viewBox="0 0 16 16"><path d="M6.5 2a5.5 4.5 0 0 1 5.4 5.5A5 4 0 0 1 6.5 11 6 6 0 0 1 4 10.6L1.5 12l.8-2.5A4.5 4.5 0 0 1 1 6.5 5.5 4.5 0 0 1 6.5 2z"/><path d="M13 7a3 3 0 0 1 2 3 3 3 0 0 1-.6 1.8l.6 2.2-2.2-1.1a5 5 0 0 1-4.6-.7A6 5 0 0 0 13 7z"/></svg>
      </label>
      <button type="button" class="submit-btn">Initiate Consultation</button>
    </form>
  </main>

  <footer class="site-footer">(C) Copyright 2026 | All Rights Reserved</footer>
</body>
</html>
```